Business Card for a Dental Office

The design should communicate integrity, quality and reliability. We also want the card look elegant, simple, but still stand out, different from the traditional-dental-office business card.

Industry/Entity Type

Business

```html
<!DOCTYPE html>
<html lang="en">
<head>
<meta charset="utf-8">
<title>Harlow Dental Studio – Business Card</title>
<link rel="stylesheet" href="https://fonts.googleapis.com/css2?family=Open+Sans:wght@400;600;700&display=swap">
<style>
  :root {
    --stage: #e7e4e0;
    --card: #1d1d1d;
    --gold: #d6b21f;
    --ink: #f2f2f2;
    --muted: #cfcfcf;
    --rule: #8a8a8a;
  }
  * { box-sizing: border-box; margin: 0; padding: 0; }
  html, body { width: 1200px; height: 814px; overflow: hidden; }
  body {
    background: var(--stage);
    font-family: "Open Sans", Arial, sans-serif;
    color: var(--ink);
    position: relative;
  }
  .card {
    position: absolute;
    top: 247px;
    width: 540px;
    height: 320px;
    background: var(--card);
    border-radius: 4px;
    box-shadow: 0 6px 18px rgba(0,0,0,.25);
  }
  .card--front { left: 40px; }
  .card--back { left: 620px; }

  .brand {
    position: absolute;
    display: flex;
    flex-direction: column;
  }
  .brand__row { display: flex; align-items: center; gap: 10px; }
  .brand__mark { width: 16px; height: 16px; background: var(--gold); }
  .brand__name {
    font-weight: 700;
    font-size: 25px;
    letter-spacing: .5px;
    text-transform: uppercase;
    color: var(--ink);
    line-height: 1;
  }
  .brand__tagline {
    margin-top: 5px;
    margin-left: 26px;
    font-weight: 700;
    font-size: 10.5px;
    letter-spacing: .6px;
    text-transform: uppercase;
    color: var(--gold);
  }
  .card--front .brand { left: 90px; top: 110px; }
  .front__web {
    position: absolute;
    left: 0; right: 0; top: 215px;
    text-align: center;
    font-size: 13px;
    letter-spacing: 3px;
    color: var(--muted);
  }

  .card--back .brand { left: 150px; top: 62px; }
  .person {
    position: absolute;
    right: 290px;
    top: 150px;
    text-align: right;
    font-size: 15px;
    line-height: 1.32;
    color: var(--ink);
  }
  .person__name { color: var(--gold); font-weight: 600; font-size: 17px; }
  .divider {
    position: absolute;
    left: 265px;
    top: 152px;
    width: 1px;
    height: 104px;
    background: var(--rule);
  }
  .contacts {
    position: absolute;
    left: 285px;
    top: 150px;
    list-style: none;
    font-size: 15px;
    line-height: 1.38;
  }
  .contacts li { display: flex; align-items: center; gap: 9px; }
  .contacts svg { width: 13px; height: 13px; fill: var(--gold); flex: none; }
</style>
</head>
<body>
  <section class="card card--front" aria-label="Card front">
    <div class="brand">
      <div class="brand__row">
        <span class="brand__mark"></span>
        <span class="brand__name">Harlow Dental Studio</span>
      </div>
      <span class="brand__tagline">Gentle care for a lasting smile</span>
    </div>
    <p class="front__web">www.harlowdental.com</p>
  </section>

  <section class="card card--back" aria-label="Card back">
    <div class="brand">
      <div class="brand__row">
        <span class="brand__mark"></span>
        <span class="brand__name">Harlow Dental Studio</span>
      </div>
      <span class="brand__tagline">Gentle care for a lasting smile</span>
    </div>

    <div class="person">
      <p class="person__name">Daniel Reyes</p>
      <p>CEO/Founder</p>
      <p>214 Willow Court</p>
      <p>Fairview, Oregon 97024</p>
    </div>

    <span class="divider"></span>

    <ul class="contacts">
      <li><svg viewBox="0 0 16 16"><path d="M3 1l3 3-1.5 2a9 9 0 005.5 5.5L12 10l3 3-2 2C7 15 1 9 1 3z"/></svg>555 214 7730</li>
      <li><svg viewBox="0 0 16 16"><path d="M4 0h8v16H4zM5.5 2v10h5V2z"/></svg>555 389 0412</li>
      <li><svg viewBox="0 0 16 16"><path d="M3 1h8v4H3zM1 6h14v7H1zM4 12h8v4H4z"/></svg>555 602 1187</li>
      <li><svg viewBox="0 0 16 16"><path d="M1 3h14v10H1zM2 4l6 5 6-5v-.5H2z" fill-rule="evenodd"/></svg>hello@harlowdental.com</li>
      <li><svg viewBox="0 0 16 16"><circle cx="8" cy="8" r="7"/></svg>www.harlowdental.com</li>
    </ul>
  </section>
</body>
</html>
```